Birchline Septic Solutions

Would like to see some single sided ones but would also like to see some double sided with one sided only being the logo. Owners name is Colin Vandro. Phone number is 555-214-0387
Services are pumping, inspections, installs, and repairs

Contact Information for Business Card

555-241-0387 Colin Vandro Maple Ridge, OH

```html
<!DOCTYPE html>
<html lang="en">
<head>
<meta charset="utf-8">
<title>Birchline Septic Solutions – Business Card</title>
<link href="https://fonts.googleapis.com/css2?family=Roboto:wght@400;700&display=swap" rel="stylesheet">
<style>
  :root {
    --stage: #3b3b3b;
    --card: #161616;
    --teal: #3cc3b8;
    --white: #ffffff;
    --soft: #d8d8d8;
    --line: #2f6f6a;
  }
  * { margin: 0; padding: 0; box-sizing: border-box; }
  html, body { width: 1200px; height: 801px; overflow: hidden; }
  body {
    background: var(--stage);
    font-family: "Roboto", Arial, sans-serif;
    position: relative;
  }
  .card {
    position: absolute;
    top: 246px;
    width: 540px;
    height: 309px;
    background: var(--card);
    border-bottom: 3px solid var(--teal);
    border-left: 2px solid var(--teal);
    overflow: hidden;
  }
  .card--front { left: 45px; }
  .card--back { left: 615px; }

  /* Front */
  .brand {
    position: absolute;
    left: 38px;
    top: 108px;
    width: 210px;
    color: var(--white);
    font-weight: 700;
  }
  .brand__name { font-size: 34px; letter-spacing: 1px; line-height: 1; }
  .brand__tag { font-size: 12px; letter-spacing: 6px; margin-top: 10px; }
  .divider {
    position: absolute;
    left: 278px;
    top: 0;
    width: 1px;
    height: 190px;
    background: var(--line);
  }
  .divider-h {
    position: absolute;
    left: 278px;
    top: 96px;
    width: 200px;
    height: 1px;
    background: var(--line);
  }
  .contact {
    position: absolute;
    left: 296px;
    top: 42px;
    color: var(--soft);
  }
  .contact__name {
    color: var(--teal);
    font-weight: 700;
    font-size: 19px;
    letter-spacing: -0.3px;
  }
  .contact__title { font-size: 13px; margin-top: 3px; }
  .contact__list { list-style: none; margin-top: 22px; }
  .contact__item {
    display: flex;
    align-items: center;
    gap: 8px;
    font-size: 13px;
    line-height: 20px;
  }
  .contact__icon { width: 10px; height: 10px; fill: var(--teal); flex: none; }

  /* Back */
  .pattern {
    position: absolute;
    inset: 0;
    background: linear-gradient(120deg, #0e0e0e 0%, #1b1b1b 45%, #2a2a2a 100%);
  }
  .back-brand {
    position: absolute;
    left: 300px;
    top: 186px;
    display: flex;
    align-items: center;
    gap: 8px;
    color: var(--white);
    font-weight: 700;
    font-size: 28px;
    letter-spacing: 1px;
  }
  .back-brand__mark { width: 10px; height: 10px; background: var(--teal); }
</style>
</head>
<body>
  <section class="card card--front" aria-label="Business card front">
    <div class="brand">
      <div class="brand__name">BIRCHLINE</div>
      <div class="brand__tag">SEPTIC SOLUTIONS</div>
    </div>
    <div class="divider"></div>
    <div class="divider-h"></div>
    <div class="contact">
      <div class="contact__name">COLIN VANDRO</div>
      <div class="contact__title">Founder / CEO</div>
      <ul class="contact__list">
        <li class="contact__item">
          <svg class="contact__icon" viewBox="0 0 10 10"><path d="M2 0.5 L3.6 2.6 L2.8 3.6 Q4 6 6.4 7.2 L7.4 6.4 L9.5 8 L8.4 9.5 Q3.5 9 0.5 1.6 Z"/></svg>
          555-241-0387
        </li>
        <li class="contact__item">
          <svg class="contact__icon" viewBox="0 0 10 10"><path d="M0 2 H10 V8.5 H0 Z M0.6 2.4 L5 5.6 L9.4 2.4" fill="var(--teal)" stroke="var(--card)" stroke-width="0.8"/></svg>
          info@birchlineseptic.com
        </li>
        <li class="contact__item">
          <svg class="contact__icon" viewBox="0 0 10 10"><circle cx="5" cy="5" r="4.6"/><path d="M0.6 5 H9.4 M5 0.4 Q2.4 5 5 9.6 Q7.6 5 5 0.4" fill="none" stroke="var(--card)" stroke-width="0.7"/></svg>
          www.birchlineseptic.com
        </li>
        <li class="contact__item">
          <svg class="contact__icon" viewBox="0 0 10 10"><path d="M5 0.3 A3.4 3.4 0 0 1 8.4 3.7 Q8.4 6 5 9.8 Q1.6 6 1.6 3.7 A3.4 3.4 0 0 1 5 0.3 Z"/><circle cx="5" cy="3.7" r="1.3" fill="var(--card)"/></svg>
          Maple Ridge, OH
        </li>
      </ul>
    </div>
  </section>

  <section class="card card--back" aria-label="Business card back">
    <div class="pattern" role="img" aria-label="Tonal gloss pattern of the repeated brand mark across the card back"></div>
    <div class="back-brand">
      <span class="back-brand__mark"></span>
      <span>BIRCHLINE</span>
    </div>
  </section>
</body>
</html>
```